KRT Engineering Business Card Design

We’re looking for an elegant, clean, and timeless business card design that communicates experience, capability, and reliability.

KRT Engineering was established in 1995 , we are a Government Contracting company providing Professional Services to the Office of Frontier Affairs, Harbor Protection and the Vantage Collective. Our capabilities include: Acquisition & Program Management; Intelligence & Security Operations; Cyber, IT & Network Operations; Lifecycle Logistics & Asset Readiness; C5ISR Systems Engineering & Sustainment.

We want the card to reflect a straightforward, confident approach to business. The design should feel polished and professional without being flashy or overly corporate.

Design Direction
Clean, sophisticated, and uncluttered
Elegant but understated
Strong typography and thoughtful spacing
A timeless aesthetic rather than something overly trendy
Confident and established, with a sense of substance
Easy to read and practical in a real-world business setting

The overall impression should be: “These are experienced professionals who know what they’re doing, do what they say, and can be relied upon.”

We’re open to creative interpretations. The finished card should feel distinctive through its typography, proportions, layout, and attention to detail rather than through excessive graphics or visual effects.

We’re looking for a design that would make a potential client immediately feel that they’re dealing with a capable, trustworthy, and established company.

Company Colors: Navy and Gold/Yellow (but you do not need to use these colors on the card)
Company Name: KRT Engineering Associates, Inc. (known as KRT Engineering)
Website: krtengineering.com
Company Logo: Navy & Gold (other variations attached)

```html
<!DOCTYPE html>
<html lang="en">
<head>
<meta charset="utf-8">
<title>KRT Engineering Business Card</title>
<link href="https://fonts.googleapis.com/css2?family=Montserrat:wght@400;500;700;800;900&display=swap" rel="stylesheet">
<style>
  :root {
    --stage: #3a3a3a;
    --card: #161616;
    --gloss: #0b0b0b;
    --gold: #f5df3c;
    --white: #ffffff;
    --text: #e9e9e9;
  }
  * { margin: 0; padding: 0; box-sizing: border-box; }
  html, body {
    width: 1200px; height: 875px; overflow: hidden;
    background: var(--stage);
    font-family: "Montserrat", sans-serif;
  }
  .canvas {
    width: 1200px; height: 875px;
    display: flex; flex-direction: column;
    align-items: center; justify-content: center; gap: 56px;
  }
  .card {
    position: relative;
    width: 560px; height: 320px;
    background: var(--card);
    border-radius: 20px;
    box-shadow: 0 3px 0 var(--gold), 0 14px 30px rgba(0,0,0,.45);
    overflow: hidden;
  }
  /* Front */
  .front { display: flex; align-items: center; justify-content: center; }
  .front .wordmark {
    font-weight: 900; font-size: 132px; letter-spacing: 2px;
    color: var(--gloss);
  }
  /* Back */
  .back { display: flex; align-items: center; padding: 0 36px 0 44px; }
  .back .brand {
    width: 220px; display: flex; align-items: center; justify-content: center;
  }
  .back .brand .wordmark {
    font-weight: 900; font-size: 70px; color: var(--white); letter-spacing: 1px;
  }
  .back .divider {
    width: 2px; height: 190px; background: var(--gold); margin: 0 26px 0 18px;
  }
  .contact { color: var(--text); font-size: 13.5px; line-height: 1.55; }
  .contact .name {
    color: var(--gold); font-weight: 800; font-size: 22px;
    letter-spacing: .5px; text-transform: uppercase; line-height: 1.1;
  }
  .contact .role { font-size: 14px; margin-bottom: 14px; }
  .contact .address { margin-bottom: 10px; }
  .contact .line { display: flex; align-items: center; gap: 8px; }
  .contact .line svg { width: 12px; height: 12px; flex: none; fill: var(--gold); }
</style>
</head>
<body>
<main class="canvas">
  <section class="card front" aria-label="Card front">
    <span class="wordmark">KRT</span>
  </section>

  <section class="card back" aria-label="Card back">
    <div class="brand"><span class="wordmark">KRT</span></div>
    <div class="divider"></div>
    <div class="contact">
      <p class="name">Marla Quenby</p>
      <p class="role">Managing Director</p>
      <p class="address">4810 Harlow Avenue, Suite<br>310, Bayport, VA 23519</p>
      <p class="line">
        <svg viewBox="0 0 12 12" aria-hidden="true"><path d="M1 4c0-2 2-3 5-3s5 1 5 3l-2 1-1-1.5H4L3 5zM2 6h8l1 5H1z"/></svg>
        757-555-0143
      </p>
      <p class="line">
        <svg viewBox="0 0 12 12" aria-hidden="true"><path d="M0 2h12v8H0zM1 3l5 4 5-4v-.2H1z" fill-rule="evenodd"/></svg>
        info@krtengineering.com
      </p>
      <p class="line">
        <svg viewBox="0 0 12 12" aria-hidden="true"><circle cx="6" cy="6" r="5.5"/></svg>
        krtengineering.com
      </p>
    </div>
  </section>
</main>
</body>
</html>
```